Brightfen Business Card Redesign & Logo Update

We need to update our business cards to something more modern and fresh. Brightfen can provide the current color schemes and old design examples, but welcome creativity in helping us with this redesign. PLEASE NOTE that we no longer utilize the "tree" and/or "leaf" imagery in our branding. If able would apprecaite an update on the quality of our "words only" logo in Ai. / PNG formats too.

Target Market(s)

Investors, landowners, corporate partners, contractors

Industry/Entity Type

Environmental Restoration & Conservation

Contact Information for Business Card

Logo, persons name, title, mailing address, phone and email, website url

Font styles to use
Other font styles liked:
• Merriweather

Requirements
Nice to have
• Logo, persons name, title, mailing address, phone and email, website url, but open to ideams
Should not have
• No all back backgrounds

```html
<!DOCTYPE html>
<html lang="en">
<head>
<meta charset="utf-8">
<title>Brightfen Business Card</title>
<link rel="stylesheet" href="https://fonts.googleapis.com/css2?family=Oswald:wght@500;600&family=Arimo:wght@400&display=swap">
<style>
  :root {
    --backdrop: #d9d9d9;
    --forest: #116b32;
    --amber: #e57a10;
    --paper: #f4f4f5;
    --ink: #1b1b1b;
    --white: #ffffff;
  }
  * { margin: 0; padding: 0; box-sizing: border-box; }
  html, body { width: 1200px; height: 793px; overflow: hidden; }
  body {
    background: var(--backdrop);
    display: flex;
    align-items: center;
    justify-content: center;
    gap: 48px;
    font-family: "Arimo", Arial, sans-serif;
  }
  .card {
    width: 540px;
    height: 309px;
    border-radius: 22px;
    position: relative;
    box-shadow: 0 8px 22px rgba(0,0,0,0.18);
  }
  .card--contact { background: var(--forest); color: var(--white); }
  .card--brand {
    background: var(--paper);
    display: flex;
    align-items: center;
    justify-content: center;
  }
  .identity {
    position: absolute;
    right: 292px;
    top: 112px;
    text-align: right;
  }
  .identity__name {
    font-family: "Oswald", sans-serif;
    font-weight: 600;
    font-size: 30px;
    line-height: 1;
    color: var(--amber);
    text-transform: uppercase;
    letter-spacing: 0.5px;
  }
  .identity__title { font-size: 13px; margin-top: 4px; }
  .divider {
    position: absolute;
    left: 270px;
    top: 92px;
    width: 1px;
    height: 92px;
    background: linear-gradient(to bottom, transparent, rgba(255,255,255,0.85), transparent);
  }
  .contact-list {
    position: absolute;
    left: 290px;
    top: 94px;
    list-style: none;
    font-size: 14px;
    line-height: 22px;
  }
  .contact-list li { display: flex; align-items: center; gap: 10px; }
  .contact-list svg { width: 13px; height: 13px; flex: none; }
  .address {
    position: absolute;
    left: 0; right: 0;
    bottom: 40px;
    text-align: center;
    font-size: 14px;
  }
  .brand-name {
    font-family: "Oswald", sans-serif;
    font-weight: 600;
    font-size: 76px;
    letter-spacing: 2px;
    color: var(--forest);
    text-transform: uppercase;
  }
</style>
</head>
<body>
  <section class="card card--contact">
    <div class="identity">
      <p class="identity__name">Daniel Mercer</p>
      <p class="identity__title">Managing Director</p>
    </div>
    <span class="divider"></span>
    <ul class="contact-list">
      <li>
        <svg viewBox="0 0 16 16" fill="var(--amber)"><path d="M4 1l3 3-2 2c1 2 3 4 5 5l2-2 3 3-2 3C7 14 2 9 1 4z"/></svg>
        555-210-4387
      </li>
      <li>
        <svg viewBox="0 0 16 16" fill="none" stroke="var(--amber)" stroke-width="2"><rect x="4" y="1" width="8" height="14" rx="1.5"/></svg>
        555-318-7602
      </li>
      <li>
        <svg viewBox="0 0 16 16"><rect x="1" y="3" width="14" height="10" rx="1" fill="var(--amber)"/><path d="M1 4l7 5 7-5" fill="none" stroke="var(--forest)" stroke-width="1.5"/></svg>
        info@brightfen.com
      </li>
      <li>
        <svg viewBox="0 0 16 16" fill="none" stroke="var(--amber)" stroke-width="1.6"><circle cx="8" cy="8" r="6.5"/><ellipse cx="8" cy="8" rx="3" ry="6.5"/><path d="M1.5 8h13"/></svg>
        www.brightfen.com
      </li>
    </ul>
    <p class="address">2140 Alder Crest Road, Juneau, Alaska 34812</p>
  </section>

  <section class="card card--brand">
    <h1 class="brand-name">Brightfen</h1>
  </section>
</body>
</html>
```